Nimbo31.com.au Website and company image design

We are looking for an exceptional website designer / company to work with our new Australian Hosting Company

Nimbo31 is a new Cloud Hosting company launching in Australia that provides Scalable, On Demand computing resources to the Australian Market Place. Scalable, On Demand ocmputing is a nice way of saying fully scalable / redundant Virtual Private Server.

We require a full company image to be developed along with a Logo and Website. There is scope for ongoing development (preferred) for the successful candidate.

Website developement will require extensive jQuery ability (sliders for ordering etc (see: http://www.hostrivo.com.au/virtual-dedicated-servers/253/kelp_vps.html).

Please communicate directly with me to establish full website scope and request further documentation / content.

Target Market(s)

Website Designers, programmers, technicians and large companies

Industry/Entity Type

It Company

Requirements
Must have
• Slider ordering system such as http://www.hostrivo.com.au/virtual-dedicated-servers/253/kelp_vps.html

Nice to have
• CMS backend system
Should not have
• Should NOT be a monster template copy!!!

```html
<!DOCTYPE html>
<html lang="en">
<head>
<meta charset="utf-8">
<title>Nimbo31 – Cloud Hosting</title>
<link rel="stylesheet" href="https://fonts.googleapis.com/css2?family=Open+Sans:wght@400;600&family=Arimo:wght@400&display=swap">
<style>
:root{
  --accent-blue:#5a93cf;
  --header-top:#3a3d40;
  --header-bottom:#000;
  --brand-red:#b3232a;
  --card-border:#d2d2d2;
  --body-text:#4a4a4a;
  --ink:#111;
  --bar-grey:#e1e1e1;
  --footer-bg:#4b5156;
  --white:#fff;
}
*{margin:0;padding:0;box-sizing:border-box}
html,body{width:1200px;height:964px;overflow:hidden;background:var(--white)}
body{position:relative;font-family:"Open Sans",sans-serif;color:var(--ink)}
.site-header{position:absolute;left:0;top:0;width:1200px;height:97px;border-top:5px solid var(--accent-blue);background:linear-gradient(var(--header-top),var(--header-bottom))}
.brand{position:absolute;left:147px;top:44px;display:flex;align-items:center;gap:8px;color:var(--white);font-size:22px;font-weight:600}
.brand-dot{width:16px;height:16px;border-radius:50%;background:var(--accent-blue)}
.main-nav{position:absolute;right:137px;top:47px;display:flex;gap:37px}
.main-nav a{color:var(--white);text-decoration:none;font-size:15px}
.hero{position:absolute;left:0;top:97px;width:1200px;height:380px}
.hero-visual{position:absolute;inset:0;background:linear-gradient(100deg,#cbd9e1 0%,#b7cbd6 40%,#9fb4c2 60%,#4e6d89 85%,#2f4a66 100%)}
.hero-title{position:absolute;left:168px;top:70px;font-size:45px;line-height:46px;font-weight:400;color:var(--ink)}
.hero-text{position:absolute;left:170px;top:172px;font-size:14px;line-height:21px;width:350px}
.btn-learn{position:absolute;left:171px;top:232px;width:145px;height:37px;background:linear-gradient(#c8262d,#a31b21);border-radius:2px;color:var(--white);font-size:16px;display:flex;align-items:center;padding-left:15px;text-decoration:none}
.btn-learn svg{position:absolute;right:12px;top:13px}
.slider-dots{position:absolute;left:172px;top:290px;display:flex;gap:5px}
.slider-dots span{width:13px;height:13px;border-radius:50%;border:2px solid var(--white)}
.slider-dots .active{background:#000;border-color:#000}
.card{position:absolute;top:493px;width:306px;height:210px;border:1px solid var(--card-border);border-radius:3px;background:linear-gradient(#fff 70%,#efefef)}
.card h2{font-size:17px;font-weight:400;color:var(--brand-red);text-align:center;margin-top:10px}
.tick-list{list-style:none;margin:26px 0 0 12px;font-family:Arimo,sans-serif;font-size:13px;color:var(--body-text)}
.tick-list li{display:flex;align-items:center;gap:12px;height:31px}
.news-date{font-family:Arimo,sans-serif;font-size:13px;margin:26px 0 0 19px}
.news-text{font-family:Arimo,sans-serif;font-size:13px;line-height:20px;color:var(--body-text);margin:9px 16px 0 18px}
.news-more{font-family:Arimo,sans-serif;font-size:13px;margin:8px 0 0 19px;display:flex;align-items:center;gap:8px;color:var(--ink)}
.trusted-title{position:absolute;left:128px;top:718px;font-size:19px;font-weight:400;color:var(--brand-red)}
.client-strip{position:absolute;left:126px;top:752px;width:948px;height:93px;border:1px solid var(--card-border);background:linear-gradient(#fff 50%,#f1f1f1);display:flex;justify-content:space-around;align-items:center;font-size:30px;color:#222}
.client-strip span{display:flex;align-items:center;gap:8px}
.client-mark{width:14px;height:14px;background:#555}
.social-bar{position:absolute;left:0;top:866px;width:1200px;height:46px;background:var(--bar-grey)}
.connect{position:absolute;left:136px;top:9px;display:flex;align-items:center;gap:8px;font-size:18px;color:#444}
.social-icon{width:21px;height:21px;border-radius:3px;background:#1a1a1a}
.connect small{font-size:13px;color:#222;margin-left:10px}
.share{position:absolute;right:142px;top:9px;font-size:18px;color:#444;display:flex;align-items:center;gap:12px}
.site-footer{position:absolute;left:0;top:912px;width:1200px;height:52px;border-top:4px solid var(--accent-blue);background:var(--footer-bg);color:var(--white);font-size:13px}
.footer-links{position:absolute;left:137px;top:15px;display:flex}
.footer-links a{color:var(--white);text-decoration:none}
.footer-links a+a::before{content:"|";margin:0 10px}
.copyright{position:absolute;right:145px;top:15px}
</style>
</head>
<body>
<header class="site-header">
  <div class="brand"><span class="brand-dot"></span>Nimbo31</div>
  <nav class="main-nav"><a href="#">Secure Cloud</a><a href="#">Compare</a><a href="#">Customers</a><a href="#">Solutions</a><a href="#">Partners</a><a href="#">Contact Us</a></nav>
</header>

<section class="hero">
  <div class="hero-visual" role="img" aria-label="Photo of a hand touching a glowing cloud icon connected by network lines"></div>
  <h1 class="hero-title">An Extremely<br>Powerful Portal</h1>
  <p class="hero-text">Lorem Ipsum is simply dummy text of the printing and typesetting industry. seorem Ipsum has been the.</p>
  <a class="btn-learn" href="#">Learn More<svg width="8" height="11" viewBox="0 0 8 11"><path d="M1 1l5 4.5L1 10" stroke="#fff" stroke-width="2" fill="none"/></svg></a>
  <div class="slider-dots"><span></span><span class="active"></span><span></span><span></span></div>
</section>

<section class="card" style="left:127px">
  <h2>Secure Cloud Configurators</h2>
  <ul class="tick-list">
    <li><svg width="18" height="16" viewBox="0 0 18 16"><path d="M1 9l5 6L17 1" stroke="#000" stroke-width="3" fill="none"/></svg>Lorem Ipsum is simply dummy text of.</li>
    <li><svg width="18" height="16" viewBox="0 0 18 16"><path d="M1 9l5 6L17 1" stroke="#000" stroke-width="3" fill="none"/></svg>Lorem Ipsum is simply dummy text of.</li>
    <li><svg width="18" height="16" viewBox="0 0 18 16"><path d="M1 9l5 6L17 1" stroke="#000" stroke-width="3" fill="none"/></svg>Lorem Ipsum is simply dummy text of.</li>
    <li><svg width="18" height="16" viewBox="0 0 18 16"><path d="M1 9l5 6L17 1" stroke="#000" stroke-width="3" fill="none"/></svg>Lorem Ipsum is simply dummy text of.</li>
  </ul>
</section>
<section class="card" style="left:447px">
  <h2>Powerful Secure Portal</h2>
  <ul class="tick-list">
    <li><svg width="18" height="16" viewBox="0 0 18 16"><path d="M1 9l5 6L17 1" stroke="#000" stroke-width="3" fill="none"/></svg>Lorem Ipsum is simply dummy text of.</li>
    <li><svg width="18" height="16" viewBox="0 0 18 16"><path d="M1 9l5 6L17 1" stroke="#000" stroke-width="3" fill="none"/></svg>Lorem Ipsum is simply dummy text of.</li>
    <li><svg width="18" height="16" viewBox="0 0 18 16"><path d="M1 9l5 6L17 1" stroke="#000" stroke-width="3" fill="none"/></svg>Lorem Ipsum is simply dummy text of.</li>
    <li><svg width="18" height="16" viewBox="0 0 18 16"><path d="M1 9l5 6L17 1" stroke="#000" stroke-width="3" fill="none"/></svg>Lorem Ipsum is simply dummy text of.</li>
  </ul>
</section>
<section class="card" style="left:768px">
  <h2>In The News</h2>
  <p class="news-date">Aug 07, 2012</p>
  <p class="news-text">Lorem Ipsum is simply dummy text of the printing and typesetting industry. Lorem Ipsum has been the industry's standard dummy text.</p>
  <a class="news-more">More News<svg width="12" height="10" viewBox="0 0 12 10"><path d="M0 3.5h6V0l6 5-6 5V6.5H0z" fill="var(--brand-red)"/></svg></a>
</section>

<h2 class="trusted-title">Trusted By</h2>
<div class="client-strip">
  <span><i class="client-mark"></i>Brightleaf</span>
  <span>Varenta</span>
  <span>northQ</span>
  <span>Kestrel</span>
  <span>tandemworks</span>
</div>

<div class="social-bar">
  <div class="connect">Connect
    <i class="social-icon" aria-label="Social link"></i><i class="social-icon" aria-label="Social link"></i><i class="social-icon" aria-label="Video link"></i><i class="social-icon" aria-label="Feed link"></i>
    <small>and more</small></div>
  <div class="share">Share<svg width="14" height="14" viewBox="0 0 14 14"><path d="M5 0h4v5h5v4H9v5H5V9H0V5h5z" fill="#111"/></svg></div>
</div>

<footer class="site-footer">
  <nav class="footer-links"><a href="#">Managed&nbsp; Hosting</a><a href="#">Cloud Hosting</a><a href="#">Application Operations</a><a href="#">Compliance</a><a href="#">Resources</a></nav>
  <div class="copyright">Copyright©nimbo31.com.au</div>
</footer>
</body>
</html>
```